Yacht, Boats, Watersports company needs a redesign of business card

Hello Designers!
We are a Boat dealership company that sells fun in the water, we sell boats, Yachts, Kayaks and also yacht WaterSport toys. We are looking to redesign our business cards in to something a little bit more sophisticated. in a way that we can make better use of our company colors. I'm attaching a zipped file containing the company 3 sets of company logo which one is an horizontal another one is a vertical and also a chromed 3d logo. Also is included two set of business cards that we use and also some designs that i think it's interesting. We use PMS 2026c Orange and PMS 7687C Blue. I would like to see at least two different options with the orange as accent and also using blue as an accent color. It's really important for the business cards to have a font option and size that is legible to most people. Our current website is wwww.coralpennant.com. Please visit if you want to have a better feeling of the Boat dealership
You can send Single sided or double side options. We are now using single sided but we may be open for a double side option if we really like the design.
Target Market(s)
Marine, boat sales, yacht sales, water toys sales/
Contact Information for Business Card
Name: Dale Whitcombe
Address: 212 North Fenwick Lane,
Pelican Cove, FL 33019
Phone: 954-731-8842
Fax: 954:731-8843
Cell: 954-382-1490
Email: dw@coralpennant.com
Website: coralpennant.com
Requirements
Must have
- the current information of the business card provided.
logo
use the PMS Colors
Nice to have
- a touch of elegance and sophistication but simple
Should not have
- should not have any typography that is hard to read, the card should be simple but yet sophisticated.

```html
<!DOCTYPE html>
<html lang="en">
<head>
<meta charset="utf-8">
<title>Coral Pennant – Business Card</title>
<link rel="stylesheet" href="https://fonts.googleapis.com/css2?family=Roboto:wght@400;500;700&family=Roboto+Condensed:wght@700&display=swap">
<style>
  :root {
    --pms-blue: #0f4477;
    --pms-orange: #ea5e2b;
    --paper: #f4f4f4;
    --ink: #2a2a2a;
    --backdrop: #e2e2e2;
    --backdrop-light: #ececec;
  }
  * { margin: 0; padding: 0; box-sizing: border-box; }
  html, body { width: 1200px; height: 960px; overflow: hidden; }
  body {
    position: relative;
    background: radial-gradient(ellipse at center, var(--backdrop-light) 0%, var(--backdrop) 70%);
    font-family: "Roboto", Arial, sans-serif;
  }
  .card {
    position: absolute;
    left: 296px;
    width: 606px;
    height: 345px;
    overflow: hidden;
    box-shadow: 2px 3px 6px rgba(0,0,0,.35);
  }
  .card--front { top: 112px; background: var(--pms-blue); }
  .card--back { top: 511px; background: var(--paper); }

  .brand-mark {
    position: absolute;
    border-radius: 50%;
  }
  .card--front .brand-mark {
    left: 253px; top: 82px; width: 100px; height: 100px;
    border: 7px solid var(--pms-orange);
  }
  .brand-name {
    position: absolute;
    font-weight: 700;
    text-transform: uppercase;
    white-space: nowrap;
  }
  .card--front .brand-name {
    left: 0; right: 0; top: 200px;
    text-align: center;
    font-size: 31px;
    letter-spacing: 6px;
    color: #ffffff;
  }
  .website {
    position: absolute;
    left: 0; right: 0; top: 292px;
    text-align: center;
    font-size: 16px;
    letter-spacing: 1.5px;
    color: #ffffff;
  }
  .website__name { color: var(--pms-orange); }

  .deco-ring {
    position: absolute;
    left: 340px; top: 28px;
    width: 290px; height: 290px;
    border-radius: 50%;
    border: 20px solid rgba(234, 94, 43, .09);
  }
  .card--back .brand-mark {
    left: 150px; top: 32px; width: 62px; height: 62px;
    border: 5px solid var(--pms-orange);
  }
  .card--back .brand-name {
    left: 46px; width: 270px; top: 104px;
    text-align: center;
    font-size: 19px;
    letter-spacing: 2.5px;
    color: var(--pms-blue);
  }
  .person-name {
    position: absolute;
    right: 38px; top: 100px;
    font-family: "Roboto Condensed", "Arial Narrow", sans-serif;
    font-weight: 700;
    font-size: 23px;
    color: var(--pms-blue);
    text-transform: uppercase;
  }
  .contact-list {
    position: absolute;
    left: 46px; top: 199px;
    list-style: none;
  }
  .contact-list li {
    display: flex;
    align-items: center;
    height: 20px;
    font-size: 16px;
    color: var(--ink);
  }
  .contact-list svg { width: 14px; height: 14px; margin-right: 6px; fill: var(--pms-orange); }
  .wave { position: absolute; left: 0; top: 0; width: 606px; height: 345px; }
  .address {
    position: absolute;
    right: 38px; top: 281px;
    text-align: right;
    font-size: 15px;
    line-height: 20px;
    color: #ffffff;
  }
</style>
</head>
<body>
  <section class="card card--front">
    <div class="brand-mark"></div>
    <div class="brand-name">Coral Pennant</div>
    <div class="website"><span class="website__name">coralpennant</span>.com</div>
  </section>

  <section class="card card--back">
    <div class="deco-ring"></div>
    <svg class="wave" viewBox="0 0 606 345" aria-hidden="true">
      <path d="M0 285 C150 318 260 300 380 272 S540 242 606 252 L606 345 L0 345 Z" fill="var(--pms-orange)"/>
      <path d="M0 322 C160 334 300 302 420 274 S560 254 606 262 L606 345 L0 345 Z" fill="#ffffff"/>
      <path d="M0 326 C160 338 300 306 420 278 S560 258 606 266 L606 345 L0 345 Z" fill="var(--pms-blue)"/>
    </svg>
    <div class="brand-mark"></div>
    <div class="brand-name">Coral Pennant</div>
    <div class="person-name">Dale Whitcombe</div>
    <ul class="contact-list">
      <li><svg viewBox="0 0 16 16"><path d="M3.5 1l3 3-1.8 2a9 9 0 0 0 5.3 5.3l2-1.8 3 3-2 2.5C7 14.5 1.5 9 1 3z"/></svg>954-731-8842</li>
      <li><svg viewBox="0 0 16 16"><path d="M4 1h8v4H4z M1 6h14v7h-3v2H4v-2H1z M5 10v4h6v-4z"/></svg>954:731-8843</li>
      <li><svg viewBox="0 0 16 16"><path d="M4 0h8a1 1 0 0 1 1 1v14a1 1 0 0 1-1 1H4a1 1 0 0 1-1-1V1a1 1 0 0 1 1-1zm1 2v10h6V2zm3 11a1 1 0 1 0 0 2 1 1 0 0 0 0-2z"/></svg>954-382-1490</li>
      <li><svg viewBox="0 0 16 16"><path d="M1 3h14v10H1zm1.5 1.5v.3L8 9l5.5-4.2v-.3zm0 2.2v4.8h11V6.7L8 10.8z"/></svg>dw@coralpennant.com</li>
    </ul>
    <div class="address">212 North Fenwick Lane<br>Pelican Cove, FL 33019</div>
  </section>
</body>
</html>
```